Design the Business card for NetVaultic

Business card required for a professional Cyber Security business.
Company Logo and Icon has already been provided however I would like other options for the logo and icon to compare to. Alternatively, please refine/enhance the image of the logo.icon I have already provided.

If you are going to use the provided logo and icon, I was thinking that the company raised Logo on White background would serve well on the front of the card. See attached. AND, a large company raised stand-alone icon to appear on black background on the back of the card with tagline 'Cyber Risk Management, Governance and Consulting' or 'Cyber Security for your Business' See attached.
Alternatively, provide your own design for the logo and icon.

Target Market(s)

Enterprise, Government, Financial.

Contact Information for Business Card

Tavin Orloweth
Founder and CEO

Email Address
Mobile Number
Website URL
LinkedIn URL

Logo Text

NetVaultic - see attached example of logo

Font styles to use
Other font styles liked:
• Berlin Sans FB

Requirements
Must have
• Clean large and bold icon on the back with tagline.
• Horizontal alignment,
Nice to have
• Round edges.
• Raised Logo/Icon
Should not have
• An unprofessional look and feel.

```html
<!DOCTYPE html>
<html lang="en">
<head>
<meta charset="utf-8">
<title>NetVaultic Business Card</title>
<link rel="stylesheet" href="https://fonts.googleapis.com/css2?family=Roboto+Condensed:wght@700&family=Roboto:wght@400&family=Signika:wght@500&display=swap">
<style>
  :root {
    --backdrop: #2b2b2c;
    --card-light: #f4f4f4;
    --card-dark: #1b1c1e;
    --brand-blue: #1a70c2;
    --soft-blue: #5677c6;
    --divider-blue: #4a72c4;
    --brand-yellow: #f4b70f;
    --text-grey: #474747;
  }
  * { margin: 0; padding: 0; box-sizing: border-box; }
  html, body { width: 1200px; height: 960px; overflow: hidden; background: var(--backdrop); }
  .canvas { position: relative; width: 1200px; height: 960px; }

  .card {
    position: absolute;
    left: 322px;
    width: 599px;
    height: 342px;
    border-radius: 18px;
  }
  .card-front { top: 108px; background: var(--card-light); }
  .card-back { top: 494px; background: var(--card-dark); }

  /* Front */
  .front-mark {
    position: absolute;
    left: 100px; top: 92px;
    width: 176px;
    text-align: center;
  }
  .front-mark .mark-dot {
    display: block;
    width: 80px; height: 80px;
    margin: 0 auto 12px;
    border-radius: 50%;
    background: var(--brand-blue);
  }
  .front-mark .mark-name {
    font-family: "Signika", sans-serif;
    font-weight: 500;
    font-size: 24px;
    color: var(--brand-blue);
  }
  .divider {
    position: absolute;
    left: 284px; top: 85px;
    width: 8px; height: 170px;
  }
  .identity { position: absolute; left: 315px; top: 101px; }
  .person-name {
    font-family: "Roboto Condensed", sans-serif;
    font-weight: 700;
    font-size: 23px;
    line-height: 26px;
    color: var(--brand-blue);
    text-transform: uppercase;
  }
  .person-title {
    font-family: "Roboto", sans-serif;
    font-size: 15px;
    line-height: 20px;
    color: var(--brand-yellow);
    text-transform: uppercase;
  }
  .contact-list { list-style: none; margin-top: 19px; }
  .contact-list li {
    display: flex;
    align-items: center;
    gap: 9px;
    height: 19px;
    font-family: "Roboto", sans-serif;
    font-size: 14.5px;
    color: var(--text-grey);
  }
  .contact-list svg { width: 14px; height: 14px; flex: none; }

  /* Back */
  .back-logo {
    position: absolute;
    left: 124px; top: 118px;
    display: flex;
    align-items: center;
    gap: 14px;
  }
  .back-logo .mark-dot {
    width: 80px; height: 80px;
    border-radius: 50%;
    background: var(--brand-blue);
  }
  .back-logo .mark-name {
    font-family: "Signika", sans-serif;
    font-weight: 500;
    font-size: 50px;
    color: var(--brand-blue);
  }
  .tagline {
    position: absolute;
    left: 0; right: 0; top: 274px;
    text-align: center;
    font-family: "Signika", sans-serif;
    font-weight: 500;
    font-size: 18px;
    color: var(--soft-blue);
  }
  .tagline .accent { color: var(--brand-yellow); }
</style>
</head>
<body>
<main class="canvas">
  <section class="card card-front">
    <div class="front-mark">
      <span class="mark-dot"></span>
      <span class="mark-name">NetVaultic</span>
    </div>
    <svg class="divider" viewBox="0 0 8 170" aria-hidden="true">
      <line x1="4" y1="4" x2="4" y2="166" stroke="var(--divider-blue)" stroke-width="2"/>
      <circle cx="4" cy="4" r="4" fill="var(--divider-blue)"/>
      <circle cx="4" cy="166" r="4" fill="var(--divider-blue)"/>
    </svg>
    <div class="identity">
      <h1 class="person-name">Tavin Orloweth</h1>
      <p class="person-title">Founder &amp; CEO</p>
      <ul class="contact-list">
        <li>
          <svg viewBox="0 0 14 14" aria-hidden="true"><rect x="3.5" y="0.5" width="7" height="13" rx="1.2" fill="none" stroke="var(--brand-blue)" stroke-width="1.5"/><rect x="5" y="2.5" width="4" height="7" fill="var(--brand-blue)"/></svg>
          555 014 2786
        </li>
        <li>
          <svg viewBox="0 0 14 14" aria-hidden="true"><rect x="1" y="3" width="12" height="8.5" fill="var(--brand-blue)"/><polyline points="1.5,3.5 7,8 12.5,3.5" fill="none" stroke="#fff" stroke-width="1.2"/></svg>
          tavin@netvaultic.com
        </li>
        <li>
          <svg viewBox="0 0 14 14" aria-hidden="true"><circle cx="7" cy="7" r="6" fill="var(--brand-blue)"/><ellipse cx="7" cy="7" rx="2.6" ry="6" fill="none" stroke="#fff" stroke-width="0.9"/><line x1="1" y1="7" x2="13" y2="7" stroke="#fff" stroke-width="0.9"/></svg>
          www.netvaultic.com
        </li>
        <li>
          <svg viewBox="0 0 14 14" aria-hidden="true"><circle cx="7" cy="7" r="6" fill="var(--brand-blue)"/></svg>
          netvaultic
        </li>
      </ul>
    </div>
  </section>

  <section class="card card-back">
    <div class="back-logo">
      <span class="mark-dot"></span>
      <span class="mark-name">NetVaultic</span>
    </div>
    <p class="tagline">Cyber Risk Management, <span class="accent">Governance &amp; Consulting</span></p>
  </section>
</main>
</body>
</html>
```